Every Shelf Set Neatly or ESN Organized needs a business card design. ESN Organized is a professi

We need a business card design that is clean, sharp and conveys a sense of organization. I already have a logo.

Target Market(s)

Families (specifically mothers), small business owners, parents, seniors

Industry/Entity Type

Business

Contact Information for Business Card

My website is www.esnorganized-example.com and my Facebook page is http://www.sociallink-example.com/everyshelfsetneatly. The phone number is 418-552-7094 and I want to be listed as Lorna M. Pelham, Owner

Requirements
Must have
• My logo.

```html
<!DOCTYPE html>
<html lang="en">
<head>
<meta charset="utf-8">
<title>ESN Organized – Business Card</title>
<link rel="stylesheet" href="https://fonts.googleapis.com/css2?family=Open+Sans:ital,wght@0,400;0,600;0,700;1,700&display=swap">
<style>
  :root {
    --bg: #e9e6e3;
    --brand-blue: #037bdb;
    --band-black: #1a1a1a;
    --ink-dark: #222222;
    --white: #ffffff;
    --photo-light: #f1eeee;
    --photo-mid: #e4dadb;
    --photo-warm: #e8c9cb;
  }
  * { box-sizing: border-box; margin: 0; padding: 0; }
  html, body {
    width: 1200px; height: 900px; overflow: hidden;
    background: var(--bg);
    font-family: "Open Sans", sans-serif;
  }
  .business-card {
    position: absolute; left: 100px; top: 140px;
    width: 1000px; height: 620px;
    display: grid;
    grid-template-columns: 486px 514px;
    grid-template-rows: 486px 134px;
    box-shadow: 0 18px 40px rgba(0,0,0,0.18);
    background: var(--white);
  }
  .brand-panel {
    position: relative;
    display: flex; align-items: center; justify-content: center;
    padding: 0 30px;
  }
  .interior-photo {
    position: absolute; inset: 0;
    background:
      radial-gradient(ellipse at 75% 70%, var(--photo-warm) 0%, transparent 45%),
      linear-gradient(160deg, var(--photo-light) 0%, var(--photo-mid) 100%);
  }
  .brand-name {
    position: relative;
    margin-top: 40px;
    font-weight: 600; font-size: 32px;
    letter-spacing: 2px;
    white-space: nowrap;
    color: var(--ink-dark);
  }
  .contact-panel {
    background: var(--brand-blue);
    color: var(--white);
    padding: 110px 0 0 36px;
  }
  .owner-name { font-weight: 700; font-size: 32px; line-height: 1.1; }
  .owner-title { font-size: 25px; line-height: 1.3; }
  .contact-list { list-style: none; margin-top: 40px; }
  .contact-item {
    display: flex; align-items: center;
    font-size: 25px; line-height: 36px;
    white-space: nowrap;
  }
  .contact-item svg { width: 20px; height: 20px; margin-right: 16px; flex: none; }
  .contact-item.social { margin-top: 36px; }
  .tagline-band {
    grid-column: 1 / 3;
    background: var(--band-black);
    color: var(--white);
    display: flex; align-items: center; justify-content: center;
    font-style: italic; font-weight: 700; font-size: 25px;
    white-space: nowrap;
  }
</style>
</head>
<body>
  <section class="business-card">
    <div class="brand-panel">
      <div class="interior-photo" role="img" aria-label="Softly blurred photo of a bright, tidy living room"></div>
      <p class="brand-name">Every Shelf Set Neatly</p>
    </div>

    <div class="contact-panel">
      <h1 class="owner-name">Lorna M. Pelham</h1>
      <p class="owner-title">Owner</p>
      <ul class="contact-list">
        <li class="contact-item">
          <svg viewBox="0 0 24 24" aria-hidden="true"><path fill="#fff" d="M6.6 10.8a15.1 15.1 0 0 0 6.6 6.6l2.2-2.2a1 1 0 0 1 1-.25 11.4 11.4 0 0 0 3.6.57 1 1 0 0 1 1 1V20a1 1 0 0 1-1 1A17 17 0 0 1 3 4a1 1 0 0 1 1-1h3.5a1 1 0 0 1 1 1c0 1.25.2 2.45.57 3.57a1 1 0 0 1-.25 1z"/></svg>
          418-552-7094
        </li>
        <li class="contact-item">
          <svg viewBox="0 0 24 24" aria-hidden="true"><rect x="3" y="6" width="18" height="12" fill="#fff"/><path d="M3 6l9 7 9-7" fill="none" stroke="#037bdb" stroke-width="1.6"/></svg>
          info@esnorganized-example.com
        </li>
        <li class="contact-item">
          <svg viewBox="0 0 24 24" aria-hidden="true"><circle cx="12" cy="12" r="9" fill="#fff"/><path d="M3 12h18M12 3c3 3 3 15 0 18M12 3c-3 3-3 15 0 18" fill="none" stroke="#037bdb" stroke-width="1.4"/></svg>
          www.esnorganized-example.com
        </li>
        <li class="contact-item social">
          <svg viewBox="0 0 24 24" aria-hidden="true"><circle cx="12" cy="12" r="6" fill="#fff"/></svg>
          /everyshelfsetneatly
        </li>
      </ul>
    </div>

    <p class="tagline-band">Every shelf, every room, every day set neatly in place</p>
  </section>
</body>
</html>
```